Association qui souhaite améliorer l'accès aux personnes en situation de handicap

Nous sommes une association qui a pour objectif d'améliorer l'accessibilité, augmenter l'offre des activités réalisables dans notre région touristique.
Nous souhaitons réaliser un site internet afin de pouvoir communiquer sur notre association. Nous avons déjà conçu notre flyer sur Plumotrix. Nous souhaiterions une base graphique se rapportant à celui-ci. C'est possible de tout retravailler mais nous souhaitons tout de même retrouver la charte graphique ou code couleur du flyer.
Il nous faudrait quelques pages:
- 1 page : Acceuil / Présentation (Home), Il y aurait le descriptif de l'association, avec ses objectifs à +/- moyen terme
- 1 page : Nos réalisations, celle-ci présenterait les éléments que nous avons réalisés avec des zones de textes et des images classées chronologiquement au fur et à mesure des nouveautés
- 1 page : Media, comme la précédente, mais ou on pourrait voir ou lire sur les divers médias qui parlent de nous
- 1 page : Evenements : c'est une page pour présenter divers activités que nous allons organiser
- 1 page : Contact qui indique comment nous contacter et avec la présentation des 5 ou 6 membres du comité
- 1 link donate : qui arrive sur un formulaire de donnée que l'on pourra faire évoluer sur un système de payement par la suite. Cette bannière doit se retrouver sur toutes les pages
Il est nécessaire que se design puisse être transféré sur une lecture sur téléphone mobile
Personnes en situation de handicap
Associatif

```html
<!DOCTYPE html>
<html lang="en">
<head>
<meta charset="utf-8">
<title>Media – Openway Association</title>
<link href="https://fonts.googleapis.com/css2?family=Raleway:wght@500;600;800&family=Mulish:wght@400;600;700&family=Bebas+Neue&display=swap" rel="stylesheet">
<style>
:root{
  --red:#c21a29;
  --red-bright:#e0202f;
  --ink:#1d1d1d;
  --text:#2b2b2b;
  --footer:#282e31;
  --footer-text:#e9ecee;
  --white:#ffffff;
}
*{margin:0;padding:0;box-sizing:border-box}
html,body{width:1200px;height:2533px;overflow:hidden;background:var(--white)}
body{position:relative;font-family:'Mulish',sans-serif;color:var(--text)}
.abs{position:absolute}

/* top bar */
.topbar{left:0;top:0;width:1200px;height:29px;background:var(--red)}
.topbar .social-dot{left:128px;top:8px;width:12px;height:12px;border-radius:50%;border:1.5px solid var(--white)}
.topbar .mail{right:128px;top:7px;color:var(--white);font-size:11px;display:flex;align-items:center;gap:5px}

/* nav */
.nav{left:0;top:29px;width:1200px;height:61px;background:var(--white)}
.brand{left:130px;top:12px;display:flex;align-items:center;gap:8px}
.brand .mark{width:14px;height:14px;background:var(--red)}
.brand .name{font-family:'Mulish',sans-serif;font-weight:700;font-size:14px;color:var(--ink);line-height:1.05;letter-spacing:.3px}
.menu{top:23px;left:538px;display:flex;gap:0;font-size:11px;font-weight:600;color:var(--ink)}
.menu span{display:block}
.menu .m1{width:72px}.menu .m2{width:134px}.menu .m3{width:72px;color:var(--red);position:relative}
.menu .m4{width:74px}.menu .m5{width:90px}
.menu .m3 svg{position:absolute;left:1px;top:15px}
.donate{left:976px;top:16px;width:94px;height:30px;border-radius:15px;background:var(--red);color:var(--white);font-size:11px;font-weight:700;display:flex;align-items:center;justify-content:center}

/* hero */
.hero{left:0;top:90px;width:1200px;height:272px;background:linear-gradient(180deg,#3b3936 0%,#4e4a43 45%,#6b5a3c 80%,#45402f 100%)}
.hero-title{left:0;top:194px;width:1200px;text-align:center;font-family:'Raleway',sans-serif;font-weight:800;font-size:33px;color:var(--red-bright)}
.crumb{left:0;top:242px;width:1200px;text-align:center;font-size:9.5px;color:#d8d8d8}
.crumb b{font-weight:400;color:var(--white)}

/* intro */
.section-title{left:0;top:422px;width:1200px;text-align:center;font-family:'Raleway',sans-serif;font-weight:500;font-size:33px;color:var(--ink)}
.intro{left:130px;top:474px;width:940px;text-align:center;font-size:13px;line-height:19.5px;color:var(--ink)}

/* media rows */
.photo{width:460px;height:291px}
.story{width:465px}
.story h2{font-family:'Raleway',sans-serif;font-weight:500;font-size:23px;color:var(--ink);margin-bottom:22px}
.story p{font-size:13px;line-height:19.5px;color:var(--text);margin-bottom:7px}

/* footer */
.footer-bg{left:0;top:2070px}
.f-brand{left:130px;top:2242px;display:flex;align-items:center;gap:8px}
.f-brand .mark{width:14px;height:14px;background:var(--white)}
.f-brand .name{font-weight:700;font-size:15px;color:var(--white);line-height:1.05}
.f-about{left:130px;top:2325px;width:215px;font-size:10.5px;line-height:16px;color:var(--footer-text)}
.f-social{left:130px;top:2384px;width:22px;height:22px;border-radius:50%;background:var(--red)}
.f-col h3{font-family:'Bebas Neue',sans-serif;font-weight:400;font-size:19px;color:var(--red-bright);letter-spacing:.5px;margin-bottom:8px}
.f-col li{list-style:none;font-size:10.5px;color:var(--footer-text);height:22.7px}
.contact-item{display:flex;gap:8px;font-size:10.5px;line-height:14px;color:var(--footer-text);margin-bottom:16px}
.contact-item .ring{flex:none;width:22px;height:22px;border-radius:50%;border:1px solid #8b9296;display:flex;align-items:center;justify-content:center}
.divider{left:130px;top:2444px;width:940px;border-top:1px dotted #4b5357}
.copy{left:0;top:2468px;width:1200px;text-align:center;font-size:10px;color:var(--footer-text)}
.copy span{color:var(--red-bright)}
</style>
</head>
<body>

<div class="abs topbar">
  <div class="abs social-dot"></div>
  <div class="abs mail">
    <svg width="12" height="9" viewBox="0 0 12 9"><rect x=".5" y=".5" width="11" height="8" fill="none" stroke="#fff"/><path d="M.5 .5 6 5l5.5-4.5" fill="none" stroke="#fff"/></svg>
    info@openway-association.ch
  </div>
</div>

<header class="abs nav">
  <div class="abs brand"><div class="mark"></div><div class="name">OPENWAY<br>ASSOCIATION</div></div>
  <nav class="abs menu">
    <span class="m1">Home</span><span class="m2">Our Achievements</span>
    <span class="m3">Media<svg width="32" height="6" viewBox="0 0 32 6"><path d="M0 1l4 4 4-4 4 4 4-4 4 4 4-4 4 4 4-4" fill="none" stroke="#c21a29" stroke-width="1.3"/></svg></span>
    <span class="m4">Events</span><span class="m5">Contacts</span>
  </nav>
  <div class="abs donate">DONATE</div>
</header>

<section class="abs hero" role="img" aria-label="Volunteer pushing a person in a wheelchair at sunset"></section>
<h1 class="abs hero-title">MEDIA</h1>
<div class="abs crumb">Home | <b>Media</b></div>

<h2 class="abs section-title">Our Media</h2>
<p class="abs intro">Sed ut perspiciatis unde omnis iste natus error sit voluptatem accusantium doloremque laudantium, totam rem aperiam, eaque ipsa quae ab illo inventore veritatis et quasi architecto beatae vitae dicta sunt explicabo.</p>

<div class="abs photo" style="left:130px;top:573px;background:linear-gradient(120deg,#5c7d2e,#2f5a3a 45%,#8fa0a8 75%,#2f4e5c)" role="img" aria-label="Carer holding the hands of an elderly man in a wheelchair outdoors"></div>
<article class="abs story" style="left:610px;top:620px">
  <h2>Accusantium Doloremque</h2>
  <p>Sed ut perspiciatis unde omnis iste natus error sit voluptatem accusantium doloremque laudantium, totam rem aperiam, eaque ipsa quae ab illo inventore veritatis et quasi architecto beatae vitae dicta sunt explicabo. Nemo enim ipsam voluptatem quia voluptas sit aspernatur aut odit aut fugit sed quia consequuntur magni.</p>
  <p>Excepteur sint occaecat cupidatat non proident, sunt in culpa qui officia deserunt mollit anim id est laborum.</p>
</article>

<article class="abs story" style="left:130px;top:981px">
  <h2>Neque Porro Quisquam</h2>
  <p>Sed ut perspiciatis unde omnis iste natus error sit voluptatem accusantium doloremque laudantium, totam rem aperiam, eaque ipsa quae ab illo inventore veritatis et quasi architecto beatae vitae dicta sunt explicabo. Nemo enim ipsam voluptatem quia voluptas sit aspernatur aut odit aut fugit sed quia consequuntur magni.</p>
  <p>Excepteur sint occaecat cupidatat non proident, sunt in culpa qui officia deserunt mollit anim id est laborum.</p>
</article>
<div class="abs photo" style="left:610px;top:935px;background:linear-gradient(160deg,#c9cdd2,#eceef0 50%,#dfe3e6)" role="img" aria-label="Two people helping a woman with crutches up in the snow"></div>

<div class="abs photo" style="left:130px;top:1296px;background:linear-gradient(100deg,#8a6a4c,#e3d5bd 30%,#cfc0a4 60%,#e7e1cf)" role="img" aria-label="Doctor checking the hearing of a seated older man"></div>
<article class="abs story" style="left:610px;top:1343px">
  <h2>Doloremque Laudantium</h2>
  <p>Sed ut perspiciatis unde omnis iste natus error sit voluptatem accusantium doloremque laudantium, totam rem aperiam, eaque ipsa quae ab illo inventore veritatis et quasi architecto beatae vitae dicta sunt explicabo. Nemo enim ipsam voluptatem quia voluptas sit aspernatur aut odit aut fugit sed quia consequuntur magni.</p>
  <p>Excepteur sint occaecat cupidatat non proident, sunt in culpa qui officia deserunt mollit anim id est laborum.</p>
</article>

<article class="abs story" style="left:130px;top:1704px">
  <h2>Neque Porro Quisquam</h2>
  <p>Sed ut perspiciatis unde omnis iste natus error sit voluptatem accusantium doloremque laudantium, totam rem aperiam, eaque ipsa quae ab illo inventore veritatis et quasi architecto beatae vitae dicta sunt explicabo. Nemo enim ipsam voluptatem quia voluptas sit aspernatur aut odit aut fugit sed quia consequuntur magni.</p>
  <p>Excepteur sint occaecat cupidatat non proident, sunt in culpa qui officia deserunt mollit anim id est laborum.</p>
</article>
<div class="abs photo" style="left:610px;top:1657px;background:linear-gradient(130deg,#c79a2c,#7e8a2a 45%,#5f8f2c 75%,#a9b04a)" role="img" aria-label="Smiling young man in a wheelchair in a sunny park"></div>

<svg class="abs footer-bg" width="1200" height="463" viewBox="0 0 1200 463"><path d="M0 90 L472 166 L1200 35 L1200 463 L0 463Z" fill="#282e31"/></svg>

<div class="abs f-brand"><div class="mark"></div><div class="name">OPENWAY<br>ASSOCIATION</div></div>
<p class="abs f-about">Sed ut perspiciatis unde omnis iste natus error sit voluptatem accusantium rem aperiam</p>
<div class="abs f-social"></div>

<div class="abs f-col" style="left:450px;top:2237px">
  <h3>Sitemap</h3>
  <ul><li>Home</li><li>Our Achivements</li><li>Media</li><li>Events</li><li>Contact Us</li></ul>
</div>
<div class="abs f-col" style="left:670px;top:2237px">
  <h3>Others</h3>
  <ul><li>Privacy Policy</li><li>Terms &amp; Conditions</li><li>Leagal</li><li>Donate</li><li>Help / Support</li></ul>
</div>
<div class="abs f-col" style="left:876px;top:2237px">
  <h3>Contacts</h3>
  <div class="contact-item">
    <div class="ring"><svg width="8" height="11" viewBox="0 0 8 11"><path d="M4 11C1 7 0 5.5 0 4a4 4 0 0 1 8 0c0 1.5-1 3-4 7z" fill="#c21a29"/><circle cx="4" cy="4" r="1.4" fill="#282e31"/></svg></div>
    <div>Chemin des Aulnes 12 / 1890<br>Val-Serein</div>
  </div>
  <div class="contact-item">
    <div class="ring"><svg width="11" height="8" viewBox="0 0 11 8"><rect width="11" height="8" fill="#c21a29"/><path d="M0 0l5.5 4.5L11 0" fill="none" stroke="#282e31"/></svg></div>
    <div style="padding-top:4px">info@openway-association.ch</div>
  </div>
</div>

<div class="abs divider"></div>
<p class="abs copy">Copyright © 2022 <span>Openway Association</span>. All Rights Reserved.</p>

</body>
</html>
```